Sophisticated, clean website reflecting my feminine, playful side to sell my abstract art,

I need a website no more than 3 pages to showcase my paintings, a little about me and some contact info. I do abstracts so looking for something a little edgy, yet feminine and current.
Updates

Hi there, These are some artists websites that I Iike: Marnelvoss.com (I like how airy it is) peterwallombry.com garethpolvens.com (I like how it scrolls) I'll need a place for a photo ( a headshot-i do not have it yet so I'll need to be able to upload that later) as well as an area for my bio. Also, it's important that I will be able to upload any new photos and descriptions easily so it should be user friendly. Lastly, I like in a sunny place so would like to have this seem upbeat and playful as that is how i like to paint. thanks-I'm trying to upload my photos now -

Target Market(s)

ppl ages 35-70 who want large scale art for their homes

Industry/Entity Type

art

Coding

Coded - Design and coding required

Number of Pages Required

3 page

Colors

Designer to choose colors to be used in the design.

Requirements
Must have
• photos of my art, a place for my bio, be easy to reach me. tasteful-nothing too "in your face" -my clients are pretty high end and organized. They like clean lines
Nice to have
• sophisticated background, muted tones in the back-similar clean font throughout-no cursive
Should not have
• too many dark areas. Too many blocks of color. Too serious.

```html
<!DOCTYPE html>
<html lang="en">
<head>
<meta charset="utf-8">
<title>Helena Marsh Art</title>
<link rel="stylesheet" href="https://fonts.googleapis.com/css2?family=Cinzel+Decorative:wght@400;700&family=Cinzel:wght@400&family=Kaushan+Script&family=Lora&family=Open+Sans:wght@400;700&display=swap">
<style>
:root{
  --orange:#ff7a00;
  --ink:#1c1c1c;
  --topbar:#e6e6e6;
  --panel:#f2f2f2;
  --card:#e8e8e8;
  --footer:#121212;
  --white:#ffffff;
  --muted:#555555;
}
*{box-sizing:border-box;margin:0;padding:0}
html,body{width:1200px;height:2987px;overflow:hidden;background:var(--white)}
body{position:relative;font-family:"Lora",serif;color:var(--ink)}
.abs{position:absolute}
.topbar{left:0;top:0;width:1200px;height:38px;background:var(--topbar);font:15px/38px "Kaushan Script",cursive;text-align:center;color:#333}
.brand{left:0;top:66px;width:1200px;text-align:center;font:700 28px "Cinzel Decorative",serif;color:var(--orange);letter-spacing:1px}
.nav{top:140px;font:17px "Kaushan Script",cursive;color:var(--ink);transform:translateX(-50%)}
.nav.active::before{content:"";position:absolute;left:0;right:0;top:-9px;height:2px;background:var(--orange)}
.cart{left:847px;top:136px;width:30px;height:30px;border:2px solid var(--orange);border-radius:50%;display:flex;align-items:center;justify-content:center}
.hero{left:0;top:189px;width:1200px;height:561px;background:linear-gradient(100deg,#e4ded3 0%,#ddd6cb 42%,#9c86b8 62%,#5a3fa8 78%,#2f2fb8 90%,#6b4f8a 100%)}
.hero-kicker{left:90px;top:290px;font:400 52px "Cinzel Decorative",serif;color:var(--ink)}
.hero-title{left:100px;top:372px;font:700 72px/90px "Cinzel Decorative",serif;color:var(--ink);text-shadow:3px 3px 4px rgba(0,0,0,.35)}
.btn{background:var(--orange);color:var(--white);border-radius:30px;display:flex;align-items:center;justify-content:center;font-family:"Cinzel Decorative",serif}
.hero-btn{left:110px;top:568px;width:133px;height:46px;font-size:22px}
.about-photo{left:99px;top:857px;width:422px;height:453px;background:linear-gradient(120deg,#6f87a6 0%,#b9b6ad 45%,#5d6048 70%,#d9d7d2 100%)}
.about-panel{left:521px;top:877px;width:578px;height:412px;background:var(--panel)}
.about-title{left:579px;top:918px;font:700 33px "Cinzel Decorative",serif}
.about-text{left:579px;top:988px;width:474px;font-size:15px;line-height:25.6px;text-align:justify;color:#333}
.about-btn{left:575px;top:1198px;width:136px;height:43px;font-size:15px}
.section-title{left:0;top:1402px;width:1200px;text-align:center;font:700 44px "Cinzel Decorative",serif}
.art{width:318px;height:318px;border-radius:4px}
.caption{width:318px;text-align:center;font:400 24px "Cinzel Decorative",serif}
.footer{left:0;top:2359px;width:1200px;height:628px;background:radial-gradient(ellipse at 30% 20%,#2a2a2a 0%,var(--footer) 60%)}
.contact-title{left:99px;top:2442px;font:400 36px "Cinzel Decorative",serif;color:var(--white);white-space:nowrap}
.contact-item{left:99px;width:340px;display:flex;align-items:flex-start;gap:14px;font:15px/26px "Open Sans",sans-serif;color:var(--white)}
.contact-icon{flex:none;width:36px;height:36px;border-radius:50%;background:var(--white);display:flex;align-items:center;justify-content:center}
.social-label{left:105px;top:2773px;font:700 15px "Open Sans",sans-serif;color:var(--white)}
.social{top:2816px;width:28px;height:28px;border-radius:50%;background:var(--orange);border:2px solid var(--white)}
.form-card{left:465px;top:2438px;width:640px;height:435px;background:var(--card);border-radius:16px}
.form-title{left:510px;top:2463px;font:400 28px "Cinzel Decorative",serif;color:#666}
.field{background:var(--white);border-radius:26px;font:12px "Lora",serif;color:var(--muted);padding:22px 25px 0}
.submit{left:521px;top:2807px;width:90px;height:43px;background:var(--orange);color:var(--white);font:16px "Open Sans",sans-serif;display:flex;align-items:center;justify-content:center;box-shadow:2px 3px 6px rgba(0,0,0,.3)}
.rule{left:99px;top:2897px;width:1000px;border-top:1px dashed #888}
.copyright{left:0;top:2936px;width:1200px;text-align:center;font:15px "Cinzel",serif;color:#ddd}
</style>
</head>
<body>
<div class="abs topbar">Lorem ipsum dolor sit amet, consectetur adipiscing elit, sed do eiusmod</div>
<div class="abs brand">Helena Marsh Art</div>
<div class="abs nav active" style="left:406px">Home</div>
<div class="abs nav" style="left:516px">About Me</div>
<div class="abs nav" style="left:641px">Abstracts</div>
<div class="abs nav" style="left:774px">Contact Us</div>
<div class="abs cart" aria-label="Cart">
  <svg width="16" height="14" viewBox="0 0 16 14"><path d="M0 1h3l2 8h8l2-6H4" fill="none" stroke="#ff7a00" stroke-width="1.8"/><circle cx="6" cy="12" r="1.3" fill="#ff7a00"/><circle cx="12" cy="12" r="1.3" fill="#ff7a00"/></svg>
</div>

<div class="abs hero" role="img" aria-label="Abstract painting with splashes of violet and blue on raw canvas"></div>
<div class="abs hero-kicker">Welcome to</div>
<div class="abs hero-title">Helena<br>Marsh Art</div>
<div class="abs btn hero-btn">Arts</div>

<div class="abs about-photo" role="img" aria-label="Photo of the artist at work in her studio beside an easel"></div>
<div class="abs about-panel"></div>
<h2 class="abs about-title">About Me</h2>
<p class="abs about-text">Sed ut perspiciatis unde omnis iste natus error sit voluptatem accusantium doloremque laudantium, totam rem aperiam, eaque ipsa quae ab illo inventore veritatis et quasi architecto beatae vitae dicta sunt explicabo. Nemo enim ipsam voluptatem quia voluptas sit aspernatur aut odit aut fugit, sed quia consequuntur magni dolores eos qui ratione voluptatem sequi nesciunt. Neque porro quisquam est, qui dolorem ipsum quia dolor sit .</p>
<div class="abs btn about-btn">Learn More</div>

<h2 class="abs section-title">Abstracts Painting</h2>
<div class="abs art" style="left:90px;top:1492px;background:linear-gradient(135deg,#e9e4d6,#c9a948 40%,#2b3f8a 65%,#e8e3d8)" role="img" aria-label="Painting: Morning Tide"></div>
<div class="abs art" style="left:435px;top:1492px;background:linear-gradient(180deg,#bcb6ad 0%,#3f86b0 18%,#a8c3d0 50%,#d8d6d1 100%)" role="img" aria-label="Painting: Rainfall"></div>
<div class="abs art" style="left:779px;top:1492px;background:radial-gradient(circle at 55% 55%,#8a4a3a,#d9a7b5 45%,#ead8d6 100%)" role="img" aria-label="Painting: Garden Waltz"></div>
<div class="abs caption" style="left:90px;top:1840px">Morning Tide</div>
<div class="abs caption" style="left:435px;top:1840px">Rainfall</div>
<div class="abs caption" style="left:779px;top:1840px">Garden Waltz</div>

<div class="abs art" style="left:90px;top:1894px;background:radial-gradient(circle at 25% 25%,#7a1e1e,#c8a09a 45%,#efe8e6 80%)" role="img" aria-label="Painting: Red Thread"></div>
<div class="abs art" style="left:435px;top:1894px;background:linear-gradient(135deg,#1f7a78,#c0722e 40%,#2a2a2a 65%,#1d6e5e)" role="img" aria-label="Painting: Open Horizons"></div>
<div class="abs art" style="left:779px;top:1894px;background:linear-gradient(135deg,#ece8e4,#6e2a1e 50%,#b58a8a 80%,#e7e2e0)" role="img" aria-label="Painting: Ember Dance"></div>
<div class="abs caption" style="left:90px;top:2242px">Red Thread</div>
<div class="abs caption" style="left:435px;top:2242px">Open Horizons</div>
<div class="abs caption" style="left:779px;top:2242px">Ember Dance</div>

<footer class="abs footer"></footer>
<h2 class="abs contact-title">Contact Info</h2>
<div class="abs contact-item" style="top:2536px">
  <span class="contact-icon"><svg width="12" height="16" viewBox="0 0 12 16"><path d="M6 0a6 6 0 0 0-6 6c0 4 6 10 6 10s6-6 6-10a6 6 0 0 0-6-6z" fill="#3b6ea8"/><circle cx="6" cy="6" r="2" fill="#fff"/></svg></span>
  <span>Lorem ipsum dolor sit amet, consectetur<br>adipiscing</span>
</div>
<div class="abs contact-item" style="top:2632px">
  <span class="contact-icon"><svg width="16" height="12" viewBox="0 0 16 12"><rect width="16" height="12" rx="1.5" fill="#3b6ea8"/><path d="M1 1l7 6 7-6" fill="none" stroke="#fff" stroke-width="1.5"/></svg></span>
  <span style="padding-top:5px">info@ helenamarshart.com</span>
</div>
<div class="abs contact-item" style="top:2698px">
  <span class="contact-icon"><svg width="14" height="14" viewBox="0 0 14 14"><path d="M3 0l3 3-2 2c1 2 3 4 5 5l2-2 3 3-2 3C6 14 0 8 0 2z" fill="#3b6ea8"/></svg></span>
  <span style="padding-top:5px">+1 555-014-2271</span>
</div>
<div class="abs social-label">SOCIAL MEDIA</div>
<span class="abs social" style="left:105px" aria-label="Social profile"></span>
<span class="abs social" style="left:148px" aria-label="Social profile"></span>
<span class="abs social" style="left:190px" aria-label="Social profile"></span>
<span class="abs social" style="left:232px" aria-label="Social profile"></span>

<div class="abs form-card"></div>
<h3 class="abs form-title">Get in Touch</h3>
<div class="abs field" style="left:504px;top:2525px;width:270px;height:53px">First Name*</div>
<div class="abs field" style="left:795px;top:2525px;width:271px;height:53px">Last Name*</div>
<div class="abs field" style="left:504px;top:2592px;width:270px;height:53px">Email*</div>
<div class="abs field" style="left:795px;top:2592px;width:271px;height:53px">Phone*</div>
<div class="abs field" style="left:504px;top:2666px;width:562px;height:118px;border-radius:30px">Tell me about your case*</div>
<div class="abs submit">SUBMIT</div>

<div class="abs rule"></div>
<div class="abs copyright">© Copyrights 2022 © Helena Marsh Art | All Rights Reserved</div>
</body>
</html>
```